holloway paving service

Needs to have phone number 0418259730 and email markholloway@brightmail.com.au.
ABN 62318470915
name mark holloway

For all your concreting solutions
Excavation
Exposed & colour concrete
House & shed slabs
Driveways
Landing & steps

Contact Information for Business Card

ph 0418259730
email markholloway@brightmail.com.au.
ABN 62318470915
name mark holloway

```html
<!DOCTYPE html>
<html lang="en">
<head>
<meta charset="utf-8">
<title>Holloway Paving Service – Business Card</title>
<link rel="stylesheet" href="https://fonts.googleapis.com/css2?family=Open+Sans:wght@400;600;700&display=swap">
<style>
  :root {
    --backdrop: #2e2825;
    --card: #151516;
    --card-edge: #1d1d1f;
    --silver: #8d8d90;
    --silver-light: #a9a9ad;
    --orange: #f26a21;
    --white: #f1f1f1;
    --rule: #55555a;
  }
  * { margin: 0; padding: 0; box-sizing: border-box; }
  html, body {
    width: 1200px; height: 864px; overflow: hidden;
    background: var(--backdrop);
    font-family: "Open Sans", Arial, sans-serif;
  }
  .canvas { position: relative; width: 1200px; height: 864px; }

  .card {
    position: absolute;
    width: 540px; height: 309px;
    background: var(--card);
    border: 1px solid var(--card-edge);
    border-radius: 3px;
    box-shadow: 0 18px 40px rgba(0,0,0,.55);
  }
  .card--front { left: 50px; top: 110px; }
  .card--back { left: 610px; top: 420px; }

  /* front */
  .front-brand {
    position: absolute; left: 0; right: 0; top: 86px;
    display: flex; justify-content: center; align-items: center; gap: 18px;
  }
  .brand-square { width: 54px; height: 54px; background: var(--silver); }
  .brand-square--accent { background: var(--orange); width: 60px; height: 60px; }
  .brand-rule { width: 1px; height: 78px; background: var(--rule); }
  .brand-text { color: var(--silver-light); }
  .brand-name {
    font-weight: 700; font-size: 17px; letter-spacing: .5px;
    text-transform: uppercase; line-height: 1.15;
  }
  .brand-name span { display: block; }
  .brand-phone { font-size: 14px; font-weight: 600; margin-top: 3px; letter-spacing: 1px; }
  .services {
    position: absolute; left: 0; right: 0; bottom: 48px;
    text-align: center; color: var(--silver-light);
    font-size: 14px; line-height: 1.55;
  }
  .services .dot { margin: 0 5px; }

  /* back */
  .back-mark {
    position: absolute; left: 68px; top: 124px;
  }
  .back-rule {
    position: absolute; left: 186px; top: 92px;
    width: 1px; height: 120px; background: var(--rule);
  }
  .contact {
    position: absolute; left: 212px; top: 90px; color: var(--white);
  }
  .contact-name {
    color: var(--orange); font-weight: 700; font-size: 19px;
    text-transform: uppercase; letter-spacing: .3px; margin-bottom: 8px;
  }
  .contact-list { list-style: none; font-size: 15px; line-height: 1.5; }
  .contact-list li { display: flex; align-items: center; gap: 9px; }
  .contact-icon { width: 14px; height: 14px; flex: none; }
  .contact-abn { margin-top: 2px; }
</style>
</head>
<body>
<main class="canvas">

  <section class="card card--front" aria-label="Card front">
    <div class="front-brand">
      <div class="brand-square"></div>
      <div class="brand-rule"></div>
      <div class="brand-text">
        <p class="brand-name"><span>Holloway Paving</span><span>Service</span></p>
        <p class="brand-phone">0418259730</p>
      </div>
    </div>
    <div class="services">
      <p>Excavation <span class="dot">•</span> Exposed &amp; colour concrete</p>
      <p>House &amp; shed slabs <span class="dot">•</span> Driveways <span class="dot">•</span> Landing &amp; steps</p>
    </div>
  </section>

  <section class="card card--back" aria-label="Card back">
    <div class="back-mark"><div class="brand-square brand-square--accent"></div></div>
    <div class="back-rule"></div>
    <div class="contact">
      <p class="contact-name">Mark Holloway</p>
      <ul class="contact-list">
        <li>
          <svg class="contact-icon" viewBox="0 0 16 16" aria-hidden="true"><path fill="#f26a21" d="M3.6 1.5l2.3 2.6-1.3 1.9c.9 2 2.5 3.6 4.5 4.5l1.9-1.3 2.6 2.3-1.2 2.3C7.3 13.5 2.5 8.7 1.3 3.7z"/></svg>
          0418259730
        </li>
        <li>
          <svg class="contact-icon" viewBox="0 0 16 16" aria-hidden="true"><rect x="1" y="3" width="14" height="10" rx="1" fill="#f26a21"/><path d="M1.5 3.8L8 8.8l6.5-5" stroke="#151516" stroke-width="1.3" fill="none"/></svg>
          markholloway@brightmail.com.au
        </li>
        <li>
          <svg class="contact-icon" viewBox="0 0 16 16" aria-hidden="true"><circle cx="8" cy="8" r="7" fill="#f26a21"/><path d="M1 8h14M8 1c-3 3.5-3 10.5 0 14M8 1c3 3.5 3 10.5 0 14" stroke="#151516" stroke-width="1.1" fill="none"/></svg>
          www.hollowaypaving.com.au
        </li>
        <li class="contact-abn">ABN 62318470915</li>
      </ul>
    </div>
  </section>

</main>
</body>
</html>
```